PostCard Design Project

I am making a mailing postcard
I am having the mailing printed using 4 color foil on certain parts.
I am looking for a design that maximizes the foil process where certain parts are done in foil to grab the customers attention (example: if there is a car on the postcard the headlights would be done in foil) .
I am targeting some industries, (auto, real estate, medical, beauty) I would like the post card to have examples of postcard ideas for 2 or 3 of these industries.
specs:
the postcard should be atleast 6.5x9 up to 8.5x11, I don't want to restrict the space for the creative as I don't want everything to look like a huge mess. both sides will be used.
the piece is a direct mail piece so it has to meet requirements of https://www.mailvantor.com/business/pdf/quick-reference-guide.pdf
text will be
"business with no limits, meet mailing with no addresses, gain new customers through "Open Porch Route Drop" reach new customers at their home without needing their address. "
I also want some current print specials I am running included.
-double your order FREE (order 500 business cards and get 1000)
-250 100lb gloss stock brochures 99.00
-business packages (cards, envelopes and letterhead) 299
-1000 flyers 140.40
-5000 postcards 179.99
A list of services
banners
booklets
brochures
business cards
calendars
catalogs
CD/DVD packages
envelopes
event tickets
flyers
hangtags
postcards
posters
presentation folders
rack cards
labels
table tents
window cling and decal
"order 24/7 orders@inkwillow.com" must be included
my logo is InkWillow will be supplied later
ive received some great designs. however Im looking for something a little more modern like some zorvel would put out. if the amount of words is too much please feel free to edit. also an idea i had for the list of services i offer is to have it transparent yet readable as the background of the postcard some small some big but covering the entire backgroud. you can then design on top of that with other thing. just an early morning thought
Reason: I have uploaded a sketch of my idea, please take time to look at it for an accurate depiction of what im looking for. feel free to add elements that make it pop off the page
Reason: We are getting close i will be providing feed back today

```html
<!DOCTYPE html>
<html lang="en">
<head>
<meta charset="utf-8">
<title>InkWillow Postcard</title>
<link rel="stylesheet" href="https://fonts.googleapis.com/css2?family=Tinos&family=Oswald:wght@500;600&family=Arimo:wght@400;700&display=swap">
<style>
  :root {
    --card: #231f20;
    --red: #e0262c;
    --frame-red: #c8202a;
    --white: #ffffff;
    --tile: #dcdcdc;
    --ink: #1a1a1a;
    --ghost: #4f4b4d;
    --gold: #c9b34a;
  }
  * { margin: 0; padding: 0; box-sizing: border-box; }
  html, body { width: 963px; height: 1200px; overflow: hidden; background: var(--card); }
  .postcard { position: relative; width: 963px; height: 1200px; background: var(--card); overflow: hidden; font-family: "Arimo", Arial, sans-serif; }

  .ghost-layer { position: absolute; inset: 0; z-index: 0; }
  .ghost-word { position: absolute; color: var(--ghost); font-size: 23px; white-space: nowrap; transform-origin: left center; }

  .headline { position: absolute; left: 20px; top: 30px; color: var(--white); font-family: "Tinos", "Times New Roman", serif; font-weight: 400; font-size: 64px; line-height: 56px; z-index: 1; }
  .headline .shine { display: block; font-size: 82px; line-height: 90px; margin-top: 8px; }

  .photo { position: absolute; border: 9px solid var(--frame-red); border-radius: 24px; overflow: hidden; z-index: 1; }
  .photo-dental { left: 513px; top: 20px; width: 423px; height: 257px; background: linear-gradient(100deg, #d9b9a6 0%, #c49a84 30%, #8c8a8c 60%, #5e5e62 100%); }
  .photo-dental .industry-tag { position: absolute; right: 36px; bottom: 16px; color: var(--gold); font-weight: 700; font-size: 34px; letter-spacing: 4px; }
  .photo-beauty { left: 271px; top: 237px; width: 300px; height: 184px; background: linear-gradient(90deg, #f2f2f2 0%, #d8b6a4 40%, #c39884 65%, #eeeeee 100%); z-index: 2; }
  .photo-auto { left: 517px; top: 301px; width: 420px; height: 294px; background: linear-gradient(135deg, #f3f3f3 0%, #c91c22 35%, #8a0f14 60%, #1c1c1c 80%, #9a9a9a 100%); }

  .logo-slot { position: absolute; left: 56px; top: 326px; color: var(--white); font-family: "Oswald", sans-serif; font-weight: 500; font-size: 31px; z-index: 1; }

  .hours { position: absolute; left: 37px; top: 468px; color: var(--white); font-family: "Oswald", sans-serif; font-weight: 600; font-size: 44px; line-height: 50px; z-index: 1; }
  .order-email { position: absolute; left: 37px; top: 520px; color: var(--red); font-family: "Oswald", sans-serif; font-weight: 600; font-size: 46px; line-height: 52px; z-index: 1; }

  .pitch { position: absolute; left: 46px; top: 638px; width: 370px; color: var(--white); font-weight: 700; font-size: 15px; line-height: 18px; z-index: 1; }

  .specials-title { position: absolute; left: 234px; top: 770px; color: var(--red); font-family: "Oswald", sans-serif; font-weight: 500; font-size: 27px; line-height: 25px; z-index: 1; }
  .special { position: absolute; background: var(--tile); border-radius: 18px; color: var(--ink); font-weight: 700; font-size: 15.5px; line-height: 19px; text-align: center; display: flex; align-items: center; justify-content: center; padding: 6px; z-index: 1; }
  .special-double { left: 42px; top: 806px; width: 187px; height: 140px; }
  .special-brochures { left: 236px; top: 861px; width: 166px; height: 125px; }
  .special-package { left: 44px; top: 955px; width: 189px; height: 142px; }
  .special-postcards { left: 240px; top: 995px; width: 145px; height: 108px; }
  .special-flyers { left: 137px; top: 1106px; width: 120px; height: 74px; }

  .services-title { position: absolute; left: 432px; top: 624px; color: var(--red); font-size: 48px; line-height: 56px; font-weight: 400; z-index: 1; }
  .services-list { position: absolute; left: 436px; top: 690px; list-style: none; color: var(--white); font-size: 19px; line-height: 30.8px; z-index: 1; }
  .services-list li { position: relative; padding-left: 18px; }
  .services-list li::before { content: ""; position: absolute; left: 0; top: 12px; width: 7px; height: 7px; border-radius: 50%; background: var(--dot); }

  .postal-panel { position: absolute; left: 694px; top: 618px; width: 233px; height: 440px; border: 2px solid var(--white); border-radius: 16px; z-index: 1; }
  .stamp-box { position: absolute; right: 16px; top: 17px; width: 81px; height: 76px; background: var(--white); border: 4px solid var(--frame-red); border-radius: 14px; }
  .postal-label { position: absolute; left: 26px; top: 124px; color: var(--white); font-weight: 700; font-size: 38px; line-height: 46px; }
</style>
</head>
<body>
<main class="postcard">
  <div class="ghost-layer" aria-hidden="true">
    <div class="ghost-word" style="left:372px;top:632px;transform:rotate(-15deg)">services</div>
    <div class="ghost-word" style="left:565px;top:628px;transform:rotate(8deg)">banners</div>
    <div class="ghost-word" style="left:384px;top:770px;transform:rotate(-8deg)">brochures</div>
    <div class="ghost-word" style="left:228px;top:738px;transform:rotate(-15deg)">booklets</div>
    <div class="ghost-word" style="left:560px;top:760px;transform:rotate(12deg)">calendars</div>
    <div class="ghost-word" style="left:170px;top:790px;transform:rotate(-12deg)">business cards</div>
    <div class="ghost-word" style="left:466px;top:800px;transform:rotate(50deg)">CD/DVD</div>
    <div class="ghost-word" style="left:392px;top:1010px;transform:rotate(20deg)">rackcards</div>
    <div class="ghost-word" style="left:330px;top:1128px;transform:rotate(10deg)">presentation folders</div>
    <div class="ghost-word" style="left:278px;top:1160px">labels</div>
  </div>

  <h1 class="headline">Let Us Help<br>Your Business<span class="shine">SHINE !</span></h1>

  <div class="photo photo-dental" role="img" aria-label="Smiling receptionist wearing a headset for a dental practice">
    <span class="industry-tag">Dental</span>
  </div>
  <div class="photo photo-beauty" role="img" aria-label="Beauty model portrait for a salon example"></div>
  <div class="photo photo-auto" role="img" aria-label="Front headlight of a red sports car for an auto dealer example"></div>

  <div class="logo-slot">LOGO HERE</div>

  <div class="hours">24 hr/ 7day</div>
  <div class="order-email">Order@inkwillow.com</div>

  <p class="pitch">Business with no limits, meet mailing with no<br>addresses, gain new customers through<br>"Open Porch Route Drop"<br>reach new customers at their home without<br>needing their address.</p>

  <div class="specials-title">current<br>specials<br>print</div>
  <div class="special special-double">Double your<br>order FREE<br>(order 500 business<br>cards and get 1000)</div>
  <div class="special special-brochures">250 100lb gloss<br>stock<br>brochures 99.00</div>
  <div class="special special-package">Business packages<br>(cards, envelopes<br>and letterhead) 299</div>
  <div class="special special-postcards">5000 postcards<br>179.99</div>
  <div class="special special-flyers">1000 flyers<br>140.40</div>

  <h2 class="services-title">Services</h2>
  <ul class="services-list">
    <li style="--dot:#3bb36a">banners</li>
    <li style="--dot:#22a9c9">booklets</li>
    <li style="--dot:#3a4fbf">brochures</li>
    <li style="--dot:#e01e6a">business cards</li>
    <li style="--dot:#f2e22c">calendars</li>
    <li style="--dot:#f07a22">catalogs</li>
    <li style="--dot:#d4741e">CD/DVD packages</li>
    <li style="--dot:#d92a2a">envelopes</li>
    <li style="--dot:#f2e22c">event tickets</li>
    <li style="--dot:#3bb36a">flyers</li>
    <li style="--dot:#4caa4c">hangtags</li>
    <li style="--dot:#1fa58c">postcards</li>
    <li style="--dot:#2a78c9">posters</li>
    <li style="--dot:#3a3f9f">presentation folders</li>
    <li style="--dot:#8a3fa8">rackcards</li>
    <li style="--dot:#c7b48a">labels</li>
  </ul>

  <div class="postal-panel">
    <div class="stamp-box"></div>
    <div class="postal-label">Postal<br>Customer</div>
  </div>
</main>
</body>
</html>
```